Psychotherapy, Life Coaching, Writer, Motivational Speaker

I am a psychotherapist, life coach, writer and speaker on health and wellness issues. I am a humanist - who believes that we are born to self-actualize - but life - changes that course. That we develop armor and coping mechanisms that divert our growth. I help people examine their road blocks to happiness. My business is unique in that I do concierge therapy. I work intensively - with multi-day sessions, I work internationally through tele-therapy - and traditionally - in an office space. My work is tailored to your needs.

Target Market(s)

Broad

Industry/Entity Type

Health

Contact Information for Business Card

Listen And Grow
Sam Perriton
248 East 39th Street
New York, NY 10027
(305) 555-0173

Requirements
Must have
• Clean lines... not too busy...
• FB page listing: Listen And Grow
• my Web page: www.listenandgrow-example.com
Nice to have
• I would love to be able to list the services: Psychotherapist, Life Coach, Motivational Speaker and Writer - but also don't want a crazy crowded card. Feel free to use the back for description.
Should not have
• Stay away from corny imagery - lotus flowers, zen, lily pond, clouds.

```html
<!DOCTYPE html>
<html lang="en">
<head>
<meta charset="utf-8">
<title>Listen And Grow – Business Card</title>
<link href="https://fonts.googleapis.com/css2?family=Lato:wght@300;400;700&display=swap" rel="stylesheet">
<style>
  :root {
    --backdrop: #e4e4e4;
    --card: #ffffff;
    --brand-blue: #4a78b5;
    --band-blue: #4f7db9;
    --ink: #111111;
    --night: #000000;
    --paper-text: #ffffff;
  }
  html, body {
    margin: 0;
    padding: 0;
    width: 1200px;
    height: 720px;
    overflow: hidden;
    background: var(--backdrop);
    font-family: "Lato", Arial, sans-serif;
  }
  .canvas {
    position: relative;
    width: 1200px;
    height: 720px;
  }
  .card {
    position: absolute;
    top: 241px;
    width: 419px;
    height: 239px;
    background: var(--card);
    border-radius: 14px;
    overflow: hidden;
  }
  .card--front { left: 148px; }
  .card--back { left: 633px; }

  .front-swoosh {
    position: absolute;
    inset: 0;
    width: 419px;
    height: 239px;
  }
  .brand-title {
    position: absolute;
    left: 13px;
    top: 36px;
    margin: 0;
    font-size: 21px;
    font-weight: 700;
    color: var(--brand-blue);
    letter-spacing: 0.1px;
  }
  .contact-list {
    position: absolute;
    left: 10px;
    top: 86px;
    margin: 0;
    padding: 0;
    list-style: none;
    font-size: 12.5px;
    color: var(--ink);
    line-height: 16px;
    white-space: nowrap;
  }
  .contact-list li {
    display: flex;
    align-items: center;
    gap: 3px;
  }
  .contact-icon {
    width: 11px;
    height: 11px;
    flex: none;
  }
  .social-mark {
    width: 10px;
    height: 10px;
    background: var(--brand-blue);
    border-radius: 1px;
    flex: none;
    margin-right: 1px;
  }
  .address {
    position: absolute;
    left: 13px;
    top: 180px;
    margin: 0;
    font-size: 12px;
    line-height: 15px;
    color: var(--ink);
    font-style: normal;
  }
  .identity {
    position: absolute;
    right: 13px;
    top: 105px;
    text-align: right;
    color: var(--paper-text);
    white-space: nowrap;
  }
  .identity__name {
    margin: 0;
    font-size: 13px;
    line-height: 18px;
  }
  .identity__name strong {
    color: var(--brand-blue);
    font-size: 15px;
    font-weight: 700;
  }
  .identity__role {
    margin: 0;
    font-size: 13px;
    line-height: 18px;
  }

  .back-title {
    position: absolute;
    left: 0;
    right: 0;
    top: 56px;
    margin: 0;
    text-align: center;
    font-size: 20px;
    font-weight: 700;
    color: var(--brand-blue);
  }
  .appointment-line {
    position: absolute;
    left: 0;
    right: 0;
    top: 132px;
    margin: 0;
    text-align: center;
    font-size: 14px;
    color: var(--ink);
  }
  .services-band {
    position: absolute;
    left: 0;
    right: 0;
    bottom: 0;
    height: 33px;
    background: var(--band-blue);
    color: var(--paper-text);
    font-size: 13.5px;
    font-weight: 300;
    display: flex;
    align-items: center;
    justify-content: center;
    letter-spacing: 0.2px;
  }
</style>
</head>
<body>
<main class="canvas">

  <section class="card card--front" aria-label="Business card front">
    <svg class="front-swoosh" viewBox="0 0 419 239" aria-hidden="true">
      <path d="M250,0 C205,65 203,170 252,239 L419,239 L419,0 Z" fill="var(--brand-blue)"/>
      <path d="M282,0 C225,55 195,165 253,239 L419,239 L419,0 Z" fill="var(--night)"/>
    </svg>

    <h1 class="brand-title">Listen And Grow</h1>

    <ul class="contact-list">
      <li>
        <svg class="contact-icon" viewBox="0 0 12 12" aria-hidden="true"><path d="M1 4.5 C1 2.5 3 1.5 6 1.5 S11 2.5 11 4.5 L8.5 5 L8 3.8 H4 L3.5 5 Z M3 6 H9 L10 10.5 H2 Z" fill="var(--brand-blue)"/></svg>
        <span>(305) 555-0173</span>
      </li>
      <li>
        <svg class="contact-icon" viewBox="0 0 12 12" aria-hidden="true"><rect x="1" y="2.5" width="10" height="7" fill="var(--brand-blue)"/><path d="M1.5 3 L6 6.5 L10.5 3" stroke="#fff" stroke-width="1" fill="none"/></svg>
        <span>sperriton@lag-example.com</span>
      </li>
      <li>
        <svg class="contact-icon" viewBox="0 0 12 12" aria-hidden="true"><circle cx="6" cy="6" r="5" fill="none" stroke="var(--brand-blue)" stroke-width="1.2"/><ellipse cx="6" cy="6" rx="2.2" ry="5" fill="none" stroke="var(--brand-blue)" stroke-width="1"/><path d="M1 6 H11" stroke="var(--brand-blue)" stroke-width="1"/></svg>
        <span>www.listenandgrow-example.com</span>
      </li>
      <li>
        <span class="social-mark" aria-hidden="true"></span>
        <span>Listen And Grow</span>
      </li>
    </ul>

    <address class="address">248 East 39th Street<br>#4N New York, NY 10027</address>

    <div class="identity">
      <p class="identity__name"><strong>Sam Perriton</strong>, LMHC, NCC</p>
      <p class="identity__role">Psychotherapist.</p>
    </div>
  </section>

  <section class="card card--back" aria-label="Business card back">
    <h2 class="back-title">Listen and Grow</h2>
    <p class="appointment-line">Your Next Appoinment is at...................... at.............. am/pm</p>
    <div class="services-band">Psychotherapy, Coaching, Wellness Media</div>
  </section>

</main>
</body>
</html>
```